Korval Advise Business Cards

We need a business card design for Korval Advise (Logo Attached), a management consultancy specialized in brand & business building.

Design should be clean, smart and a touch of innnovation without being gimmicky.

The details on the card should be:
Name: Tomas Velduren
Title: Managing Director
Address: 42 Marlowe Pier, Tarn Vessel Tower, Singapore 073926
Tel: +6285927461082
email: tv@korvaladvise.example
website: korvaladvise.example

For further background on corporate identity, please check www.korvaladvise.example
Updates

Dear all,

Many thanks for the submissions so far! I gave feedback to those designs that I prefer at this stage.

Overall I see that my preference goes into the direction that 'less is more' and 'simple is beautiful'

Please create uniqueness and standout by the simplicity and attraction of the overall concept and design.

Many thanks and please shout incase of questions!

Tomas

Industry/Entity Type

Business

```html
<!DOCTYPE html>
<html lang="en">
<head>
<meta charset="utf-8">
<title>Korval Advise Business Cards</title>
<link rel="stylesheet" href="https://fonts.googleapis.com/css2?family=Open+Sans:wght@400;600;700&display=swap">
<style>
  :root {
    --orange: #ff6a00;
    --charcoal: #4a4a4a;
    --white: #ffffff;
    --backdrop: #ece9e4;
    --title-orange: #f07814;
  }
  * { margin: 0; padding: 0; box-sizing: border-box; }
  html, body { width: 1173px; height: 1200px; overflow: hidden; }
  body {
    background: var(--backdrop);
    font-family: "Open Sans", Arial, sans-serif;
    position: relative;
  }
  .card {
    position: absolute;
    width: 942px;
    height: 537px;
    border-radius: 36px;
    overflow: hidden;
    box-shadow: 0 4px 14px rgba(0,0,0,0.25);
  }
  .card-front { left: 20px; top: 45px; background: var(--white); }
  .card-back { left: 215px; top: 622px; background: var(--orange); }
  .front-shapes { position: absolute; inset: 0; width: 100%; height: 100%; }

  .brand-name {
    position: absolute;
    font-weight: 600;
    font-size: 80px;
    letter-spacing: -1px;
    line-height: 1;
    white-space: nowrap;
  }
  .card-front .brand-name { left: 43px; top: 92px; color: var(--charcoal); }
  .card-back .brand-name { left: 0; right: 0; top: 190px; text-align: center; color: var(--white); }

  .holder { position: absolute; left: 49px; top: 244px; }
  .holder-name { font-weight: 700; font-size: 27px; color: var(--charcoal); line-height: 1.25; }
  .holder-title { font-weight: 400; font-size: 22px; color: var(--title-orange); line-height: 1.35; }

  .contact-list {
    position: absolute; right: 20px; top: 335px;
    list-style: none; color: var(--white);
    font-size: 22px; line-height: 41px;
  }
  .contact-list li { display: flex; align-items: center; justify-content: flex-end; gap: 8px; }
  .contact-icon { width: 20px; height: 20px; }
  .address {
    position: absolute; right: 20px; top: 492px;
    color: var(--white); font-size: 22px; line-height: 30px;
  }
  .back-url {
    position: absolute; left: 0; right: 0; top: 370px;
    text-align: center; color: var(--white);
    font-size: 24px; letter-spacing: 4px;
  }
</style>
</head>
<body>
  <section class="card card-front" aria-label="Card front">
    <svg class="front-shapes" viewBox="0 0 942 537" preserveAspectRatio="none" aria-hidden="true">
      <path d="M0 472 C 250 530, 600 400, 942 22 L942 537 L0 537 Z" fill="var(--charcoal)"/>
      <path d="M0 392 C 200 470, 480 420, 662 297 C 470 440, 220 492, 0 456 Z" fill="var(--orange)"/>
    </svg>

    <p class="brand-name">Korval Advise</p>

    <div class="holder">
      <p class="holder-name">Tomas Velduren</p>
      <p class="holder-title">Managing Director</p>
    </div>

    <ul class="contact-list">
      <li>
        <svg class="contact-icon" viewBox="0 0 20 20" aria-hidden="true"><circle cx="10" cy="10" r="8.5" fill="none" stroke="#fff" stroke-width="1.5"/><path d="M7 5.5 l2 2.5 -1.2 1.2 a6 6 0 0 0 3 3 l1.2-1.2 2.5 2 -1.3 1.5 c-3 0-7-4-7-7z" fill="#fff"/></svg>
        <span>+6285927461082</span>
      </li>
      <li>
        <svg class="contact-icon" viewBox="0 0 20 20" aria-hidden="true"><path d="M3 8 L10 3 L17 8 V16 H3 Z" fill="#fff"/><path d="M3 8 L10 12.5 L17 8" fill="none" stroke="var(--charcoal)" stroke-width="1.4"/></svg>
        <span>tv@korvaladvise.example</span>
      </li>
      <li>
        <svg class="contact-icon" viewBox="0 0 20 20" aria-hidden="true"><g fill="none" stroke="#fff" stroke-width="1.4"><circle cx="10" cy="10" r="8"/><ellipse cx="10" cy="10" rx="3.5" ry="8"/><path d="M2 10 H18 M3.5 6 H16.5 M3.5 14 H16.5"/></g></svg>
        <span>www.korvaladvise.example</span>
      </li>
    </ul>

    <p class="address">42 Marlowe Pier, Tarn Vessel Tower, Singapore 073926</p>
  </section>

  <section class="card card-back" aria-label="Card back">
    <p class="brand-name">Korval Advise</p>
    <p class="back-url">www.korvaladvise.example</p>
  </section>
</body>
</html>
```